New Business Card Design Project LORVANTI-Italy

we are LORVANTI-Italy
our company in the market for 3 years we are luxury cosmetic company and its about time for a facelift :)
i will like to have elegant luxurious and unique business card
that will give the person that get it a unique, luxurious and elegant impression
I'm VERY OPEN FOR NEW IDEAS , even duo i add a few files of things that i see on line and i like them

i add my logo as well
my website is LORVANTI.COM
(if you would like to see the main style that we have)

Target Market(s)

adult that have money :)

Industry/Entity Type

Business

Contact Information for Business Card

Name - Dario Lorvanti
Position - CEO and CO Founder
address - 4817 E Halvern
telephone - 555-384-1926
email - dario@lorvanti.com
fax - 555-384-1926
website - LORVANTI.COM

Colors
000000
959595
fbee3e
ffffff

Requirements
Must have
• big logo in GOLD color
• elegant look
• impressive
Nice to have
• not must but maybe classy pattern background
• not must but maybe emblem
• maybe clear plastic business card
Should not have
• colors
• images

```html
<!DOCTYPE html>
<html lang="en">
<head>
<meta charset="utf-8">
<title>LORVANTI Italy – Business Card</title>
<link rel="stylesheet" href="https://fonts.googleapis.com/css2?family=Cinzel:wght@500;600&family=Open+Sans:wght@400&display=swap">
<style>
  :root {
    --stage: #e9e6e1;
    --card-black: #0b0b0b;
    --card-charcoal: #1c1c1c;
    --pattern-dark: #202020;
    --pattern-light: #2c2c2c;
    --gold: #d9b13b;
    --grey: #959595;
    --white: #ffffff;
    --emboss: #2a2a2a;
  }
  * { box-sizing: border-box; margin: 0; padding: 0; }
  html, body {
    width: 1200px; height: 900px; overflow: hidden;
    background: var(--stage);
  }
  .stage {
    position: relative; width: 1200px; height: 900px;
    display: flex; align-items: center; justify-content: center; gap: 40px;
  }
  .card {
    position: relative; width: 540px; height: 309px;
    border-radius: 3px; overflow: hidden;
    box-shadow: 0 10px 28px rgba(0,0,0,.28);
  }

  /* Front side */
  .card--front { background: var(--pattern-dark); }
  .card__pattern {
    position: absolute; inset: 0;
    background: radial-gradient(ellipse at 50% 40%, var(--pattern-light), var(--pattern-dark) 75%);
  }
  .front__mark {
    position: absolute; left: 50%; top: 32px; transform: translateX(-50%);
    width: 92px; height: 92px; border-radius: 50%;
    border: 3px solid var(--gold);
  }
  .wordmark {
    position: absolute; text-align: center;
    font-family: "Cinzel", "Times New Roman", serif;
    color: var(--gold);
  }
  .wordmark__name { font-weight: 600; letter-spacing: 1px; line-height: 1; }
  .wordmark__rule { height: 2px; background: var(--gold); }
  .wordmark__place { font-weight: 600; letter-spacing: 2px; }

  .card--front .wordmark { left: 112px; right: 112px; top: 150px; }
  .card--front .wordmark__name { font-size: 46px; }
  .card--front .wordmark__rule { margin: 8px 0 6px; }
  .card--front .wordmark__place { font-size: 14px; }

  /* Back side */
  .card--back {
    background: radial-gradient(ellipse at 60% 25%, var(--card-charcoal), var(--card-black) 70%);
  }
  .card--back .wordmark { left: 38px; width: 250px; top: 34px; }
  .card--back .wordmark__name { font-size: 40px; }
  .card--back .wordmark__rule { margin: 6px 0 5px; }
  .card--back .wordmark__place { font-size: 13px; }

  .back__emblem {
    position: absolute; right: 70px; top: 40px;
    width: 112px; height: 112px; border-radius: 50%;
    border: 2px solid var(--emboss);
    box-shadow: inset 0 1px 2px rgba(255,255,255,.06);
  }
  .person { position: absolute; left: 38px; top: 150px; }
  .person__name {
    font-family: "Cinzel", "Times New Roman", serif; font-weight: 600;
    font-size: 19px; color: var(--gold); letter-spacing: .5px;
  }
  .person__role {
    font-family: "Open Sans", Arial, sans-serif; font-size: 12px;
    color: var(--white); margin-top: 2px;
  }
  .contacts {
    position: absolute; left: 38px; top: 212px; list-style: none;
    font-family: "Open Sans", Arial, sans-serif; font-size: 13px; color: var(--white);
  }
  .contacts li { display: flex; align-items: center; gap: 8px; height: 19px; }
  .contacts svg { width: 11px; height: 11px; fill: var(--gold); flex: none; }
  .address {
    position: absolute; right: 26px; bottom: 110px;
    display: flex; align-items: center; gap: 6px;
    font-family: "Open Sans", Arial, sans-serif; font-size: 11px; color: var(--white);
  }
  .address svg { width: 10px; height: 13px; fill: var(--gold); }
</style>
</head>
<body>
<main class="stage">

  <section class="card card--front" aria-label="Card front">
    <div class="card__pattern" role="img" aria-label="Tone-on-tone embossed repeating emblem pattern on black"></div>
    <div class="front__mark"></div>
    <div class="wordmark">
      <div class="wordmark__name">LORVANTI</div>
      <div class="wordmark__rule"></div>
      <div class="wordmark__place">ITALY</div>
    </div>
  </section>

  <section class="card card--back" aria-label="Card back">
    <div class="wordmark">
      <div class="wordmark__name">LORVANTI</div>
      <div class="wordmark__rule"></div>
      <div class="wordmark__place">ITALY</div>
    </div>
    <div class="back__emblem"></div>

    <div class="person">
      <div class="person__name">DARIO LORVANTI</div>
      <div class="person__role">CEO and CO Founder</div>
    </div>

    <ul class="contacts">
      <li>
        <svg viewBox="0 0 12 12" aria-hidden="true"><path d="M2.4 0.8l1.8 2.1-1 1.2c.7 1.5 1.9 2.7 3.4 3.4l1.2-1 2.1 1.8-.9 2.2C5.4 10.3 1.5 6.4 0.3 1.7z"/></svg>
        <span>555-384-1926</span>
      </li>
      <li>
        <svg viewBox="0 0 12 12" aria-hidden="true"><path d="M3 0h5l1 1v3H3zM1 4.5h10v6H1zM3 6v1h2V6zm3 0v1h3V6zM3 8v1h2V8zm3 0v1h3V8z"/></svg>
        <span>555-384-1926</span>
      </li>
      <li>
        <svg viewBox="0 0 12 12" aria-hidden="true"><path d="M0 2h12v8H0zm1 1v.3l5 3.4 5-3.4V3zm0 1.5V9h10V4.5L6 8z"/></svg>
        <span>dario@lorvanti.com</span>
      </li>
      <li>
        <svg viewBox="0 0 12 12" aria-hidden="true"><path d="M6 0a6 6 0 1 0 0 12A6 6 0 0 0 6 0zm0 1.2c.6.6 1.1 1.6 1.3 2.8H4.7C4.9 2.8 5.4 1.8 6 1.2zM1.4 5h2.1v2H1.4zm7.1 0h2.1v2H8.5zM4.6 5h2.8v2H4.6zm.1 3h2.6C7.1 9.2 6.6 10.2 6 10.8 5.4 10.2 4.9 9.2 4.7 8z"/></svg>
        <span>www.lorvanti.com</span>
      </li>
    </ul>

    <div class="address">
      <span>4817 E Halvern</span>
      <svg viewBox="0 0 10 13" aria-hidden="true"><path d="M5 0a5 5 0 0 0-5 5c0 3.5 5 8 5 8s5-4.5 5-8a5 5 0 0 0-5-5zm0 7a2 2 0 1 1 0-4 2 2 0 0 1 0 4z"/></svg>
    </div>
  </section>

</main>
</body>
</html>
```